Dietary supplement, Clean and simple.

Hi,
I’d like to talk about the project,

About us:
We are a dietary supplement (Vitamins, Minerals, amino acids etc.) company.
The goal is to have about 25 products at the end of this year. However, for this goal to be achieved we need a good label design to make our products represent our company values.
I’ll be here every day supporting your questions, we are fully committed to making the highest/best quality/customer experience possible.

About the design and our values:
- Professional (We are in the industry of professionalism and expertise. I would love to show we are competent at this, Id. Like to have the labels looks like we have done our research.)
- Efficient (White spacing, good use of the space available.)
- Simple (Straight forward, in 5 seconds they have to know what the product they have is/how functions. We’re trying to simplify it for the consumer.
- No distractions (the only visually “distracting” factor can be the vector art.)

The guidelines:
The goal is to have a universal design, with one element that changes (Vector art). I’ll attach a file/multiple files I think can show some visuals on what I’m looking for, and what parts of the design I think are good/bad.

Label size: 69x155mm (Front is 77.5mm)

Design whatever you think fits our image. You’re the design expert, all I care about is that it fits our company standards/image.

Use this color/font.
Font: Sans Serif
Main company color is Mind green #237D62 (Use this color for something in the design.)

What I thought would be cool/might looks ugly, who knows:
1. The front of the label: Should have 1 vector art, preferably in the top right corner. (That looks good in multiple colors. The vector can have multiple areas to color, I would prefer 2 main colors in the vector art. The interchangeable colors are used for multiple kinds of products.)
2. Text/product information on the left. The text that will have to be displayed:
- Product name for instance “Magnesium + B6”
- Description for the product for instance “Magnesium with ginger taste”
- Company name or logo. (Add ® behind it. We are soon to be trademark registered.)
3. We need to show the "daily intake" amount on the front and also the amount in the complete bottle. For instance, “Daily intake 1 capsule, 60 capsules”.
• You don’t have to design the backside of the label. After I chose a design, I’d like to chat and give specific information on what areas need to be assigned where. (Too complex because of the law.)
Updates

Hi, Please make the deadline 31 days total. I want designers to have the time to design. And not be rushed to finish it.

I want to extend the deadline because i feel like a slightly more medical look would be interesting. Hope you can come up with something!!

Target Market(s)

Dietary supplement consumers

Industry/Entity Type

Dietary supplements

Font styles to use
Sans Serif

Colors

Designer to choose colors to be used in the design.

Requirements
Must have
• Trademark icon "®" has to be at the top right after the company logo(text of logo)/name.

```html
<!DOCTYPE html>
<html lang="en">
<head>
<meta charset="utf-8">
<title>Magnesium + B6 Label</title>
<link href="https://fonts.googleapis.com/css2?family=Noto+Sans:wght@400;600;700&display=swap" rel="stylesheet">
<style>
  :root {
    --page-bg: #e8e8e8;
    --band-green: #87b6a8;
    --wave-green: #7db48a;
    --brand-green: #237d62;
    --title-ink: #222222;
    --pill-yellow: #d0c22e;
    --badge-teal: #1e9aa3;
    --white: #ffffff;
  }
  html, body {
    margin: 0;
    padding: 0;
    width: 1200px;
    height: 1200px;
    overflow: hidden;
    background: var(--page-bg);
    font-family: "Noto Sans", Arial, sans-serif;
  }
  .canvas {
    position: relative;
    width: 1200px;
    height: 1200px;
  }
  .label {
    position: absolute;
    left: 133px;
    top: 390px;
    width: 934px;
    height: 419px;
    background: var(--white);
    overflow: hidden;
  }
  .label-band {
    position: absolute;
    left: 0;
    top: 0;
    width: 934px;
    height: 252px;
    background: var(--band-green);
  }
  .wave-art {
    position: absolute;
    inset: 0;
    background: linear-gradient(160deg, var(--band-green) 0%, var(--wave-green) 45%, var(--band-green) 80%);
  }
  .brand-seal {
    position: absolute;
    left: 383px;
    top: 10px;
    width: 180px;
    height: 180px;
    border-radius: 50%;
    background: var(--white);
    box-shadow: 6px 2px 0 rgba(60, 110, 95, 0.55);
    display: flex;
    align-items: center;
    justify-content: center;
  }
  .brand-name {
    color: var(--brand-green);
    font-weight: 700;
    font-size: 24px;
    letter-spacing: 0.5px;
    white-space: nowrap;
  }
  .brand-name sup {
    font-size: 10px;
    vertical-align: top;
    margin-left: 1px;
  }
  .product-title {
    position: absolute;
    left: 269px;
    top: 210px;
    margin: 0;
    font-size: 42px;
    font-weight: 600;
    color: var(--title-ink);
    letter-spacing: 0.3px;
    line-height: 1;
  }
  .product-flavour {
    position: absolute;
    left: 269px;
    top: 260px;
    height: 25px;
    padding: 0 9px;
    border-radius: 7px;
    background: var(--pill-yellow);
    color: var(--title-ink);
    font-size: 18px;
    line-height: 25px;
    white-space: nowrap;
  }
  .product-type {
    position: absolute;
    left: 275px;
    top: 360px;
    color: var(--brand-green);
    font-size: 18px;
    font-weight: 700;
    letter-spacing: 0.4px;
    line-height: 1.2;
  }
  .count-badge {
    position: absolute;
    left: 539px;
    top: 291px;
    width: 94px;
    height: 94px;
  }
  .count-badge text {
    font-family: "Noto Sans", Arial, sans-serif;
  }
</style>
</head>
<body>
<div class="canvas">
  <section class="label">
    <div class="label-band">
      <div class="wave-art" role="img" aria-label="Decorative flowing green wave swooshes across the band"></div>
    </div>
    <div class="brand-seal">
      <span class="brand-name">CALM CREST<sup>®</sup></span>
    </div>
    <h1 class="product-title">MAGNESIUM + B6</h1>
    <div class="product-flavour">Magnesium with ginger taste</div>
    <div class="product-type">DIETARY SUPPLEMENT</div>
    <svg class="count-badge" viewBox="0 0 94 94" aria-label="60 capsules">
      <defs>
        <radialGradient id="badgeShell" cx="50%" cy="40%" r="60%">
          <stop offset="0%" stop-color="#ffffff"/>
          <stop offset="100%" stop-color="#c9c9c9"/>
        </radialGradient>
      </defs>
      <circle cx="47" cy="47" r="46" fill="url(#badgeShell)"/>
      <circle cx="47" cy="44" r="37" fill="var(--badge-teal)"/>
      <circle cx="47" cy="44" r="32" fill="var(--white)"/>
      <text x="47" y="50" text-anchor="middle" font-size="27" font-weight="700" fill="var(--title-ink)">60</text>
      <text x="47" y="63" text-anchor="middle" font-size="9" fill="var(--title-ink)">CAPSULES</text>
    </svg>
  </section>
</div>
</body>
</html>
```